Bootstrap site for Cloud Services company

Hi,

First I'd like you to submit you design of the homepage. If you are the winner, I'll get you do design the rest and code it up in HTML, CSS etc using bootstrap.

Why bootstrap? This will probably mean
that you understand the fundamentals of CSS and know how to
make a good-looking website. Also should mean that you can throw
together this site relatively easily so you can focus on the design
work. I'll need some icons and banner style images done.

There's no server-side coding involved, and there's also no content to write, just put placemarker text wherever appropriate. You must be familiar with bootstrap.

Our business sells Velmora Suite for Business and IT support services.

The icon for our business is attached.

Basically I want you to go by the design of this site
http://lnk.example-short.net/qR7x

However, don't just copy it. I want it to be of a similar layout and
style, but be creative.

I like the simplicity and how it's easy to follow visually.

Just submit the homepage, and if you're successful, I'll get you to
design the rest of the pages for me and code up the pages.

Thanks!

Target Market(s)

We are marketing towards businesses that need their IT managed for them.

Industry/Entity Type

Business

Requirements
Must have
• I like how clean and nice the roboto font is, but it's up to you.

You're welcome to take inspiration from the 'Tarvix Pulse' layout and design. Nice use of white space and layout.

Menu headings at the top are as follows:
Support | Deployment | Training | Development | Contact Us |
About

Home page:

In a similar style of the referenced webpage http://lnk.example-short.net/qR7x, I'd
like a single banner that says "Brisbane's leading Velmora Suite
specialists". In the banner have a computer screen or laptop and a
tablet or smartphone with some 'velmora suite for business' style of
logos coming out of it be creative with some nice design.

Under that, 3 square (or something) icons.
Save Money | Collaborate | Grow
just put some placemarker text in it in a similar fashion to the
reference site.

Just throw some other things in there to fill it up a bit.
Should not have
• http://lnk.example-short.net/qR7x
I don't want the scrolling banner with the site above, static is fine.

I don't like how when the menu is moused-over, the whole page
moves down.

No stock photos of 'successful business people' or 'very attractive
telephone operator waiting to take your call' :)

```html
<!DOCTYPE html>
<html lang="en">
<head>
<meta charset="utf-8">
<title>Cloudvane – Brisbane's leading Velmora Suite specialists</title>
<link href="https://fonts.googleapis.com/css2?family=Roboto:ital,wght@0,300;0,400;0,500;0,700;1,400&family=Roboto+Condensed:ital,wght@0,400;0,700;1,400&display=swap" rel="stylesheet">
<style>
:root{
  --ink:#2b2b2b;
  --muted:#7d7d7d;
  --navy:#1f2a6b;
  --accent:#f5a90c;
  --blue:#1e73bb;
  --nav-blue:#2a8fd6;
  --green:#6cb52d;
  --orange:#f6a70d;
  --band:#e6e6e6;
  --footer:#4a4a4a;
  --banner-dark:#3f3f3f;
  --banner-mid:#8a8a8a;
  --line:#e2e2e2;
}
*{box-sizing:border-box;margin:0;padding:0}
html,body{width:1200px;height:2231px;overflow:hidden}
body{position:relative;background:#fff;font-family:'Roboto',Arial,sans-serif;color:var(--ink)}
.abs{position:absolute}
.cond{font-family:'Roboto Condensed','Roboto',Arial,sans-serif}

/* header */
.site-header{left:0;top:0;width:1200px;height:90px;background:linear-gradient(#fff,#ececec)}
.brand{display:flex;align-items:center;gap:12px}
.brand-dot{width:44px;height:44px;border-radius:50%;background:var(--navy)}
.brand-name{font-size:34px;font-weight:700;color:var(--navy);letter-spacing:.5px}
.main-nav{left:475px;top:34px;display:flex;gap:0}
.main-nav a{font-family:'Roboto Condensed',Arial,sans-serif;font-size:15px;text-transform:uppercase;color:#333;text-decoration:none;height:34px;line-height:34px;padding:0 15px}
.main-nav a.active{background:var(--nav-blue);color:#fff;border-radius:17px;box-shadow:inset 0 -2px 0 rgba(0,0,0,.15)}

/* banner */
.hero{left:0;top:90px;width:1200px;height:395px;background:radial-gradient(ellipse at 30% 55%,var(--banner-mid) 0%,#5a5a5a 45%,var(--banner-dark) 100%)}
.hero-art{left:190px;top:22px;width:370px;height:360px;border-radius:24px;background:linear-gradient(135deg,#2e2e2e 0%,#595959 40%,#e64a3b 60%,#3aa0e0 75%,#f4c21a 90%);opacity:.9}
.hero-title{right:68px;top:110px;text-align:right;background:linear-gradient(90deg,rgba(0,0,0,0),rgba(0,0,0,.35) 20%);padding:14px 10px 14px 40px}
.hero-title .l1{font-size:49px;color:#fff;letter-spacing:1px;line-height:1;font-weight:400}
.hero-title .l2{font-size:37px;color:#fff;line-height:1.2;margin-top:6px;letter-spacing:1px}
.hero-title .l2 span{color:var(--accent)}

/* intro */
.intro{left:0;top:505px;width:1200px;text-align:center}
.intro h1{font-size:26px;font-weight:700;color:#222}
.intro p{font-size:14.5px;color:var(--muted);line-height:18px;margin-top:12px}
.btn-dark{display:inline-block;margin-top:18px;background:linear-gradient(#3a3a3a,#111);color:#fff;font-size:15px;font-weight:700;padding:0 20px;height:38px;line-height:38px;border-radius:3px}
.divider-shadow{left:100px;top:660px;width:1000px;height:14px;background:radial-gradient(ellipse at 50% 0%,rgba(0,0,0,.14),rgba(0,0,0,0) 70%)}

/* feature tiles */
.tile{top:712px;width:300px;height:143px;color:#fff;padding:14px}
.tile-blue{left:141px;background:var(--blue)}
.tile-green{left:450px;background:var(--green)}
.tile-orange{left:759px;background:var(--orange)}
.tile svg{position:absolute;left:22px;top:14px}
.tile h3{position:absolute;left:14px;bottom:16px;font-size:19px;font-weight:400}
.tile p{position:absolute;left:127px;top:12px;width:165px;font-family:'Roboto Condensed','Roboto',Arial,sans-serif;font-size:13px;font-weight:700;line-height:20px}

/* services band */
.band{left:0;top:892px;width:1200px;height:282px;background:var(--band)}
.svc{top:935px;width:280px;text-align:center}
.svc h2{font-family:'Roboto Condensed',Arial,sans-serif;font-size:19px;color:#222;font-weight:400;text-transform:uppercase}
.svc p{font-size:13px;color:#777;line-height:20.5px;margin-top:18px}
.btn-light{display:inline-block;margin-top:20px;width:206px;height:37px;line-height:37px;background:linear-gradient(#f7f7f7,#d8d8d8);border-radius:2px;font-family:'Roboto Condensed',Arial,sans-serif;font-size:15px;color:#333;box-shadow:0 12px 10px -10px rgba(0,0,0,.35)}

/* news columns */
.col{top:1205px;width:441px}
.col-head{display:flex;align-items:center;gap:10px;height:24px}
.col-head h2{font-family:'Roboto Condensed',Arial,sans-serif;font-size:19px;font-weight:700;color:#333;white-space:nowrap}
.col-head h2 span{color:var(--accent)}
.col-head em{font-size:11px;color:#999;white-space:nowrap}
.col-head i{flex:1;height:9px;background:#ebebeb}
.entry{position:relative;height:152px;border-bottom:2px solid var(--line)}
.entry:last-of-type{border-bottom:none}
.thumb{position:absolute;left:0;top:27px;width:67px;height:68px;background:linear-gradient(135deg,#1b1b1b,#3d6fd1 45%,#e0b422 70%,#1b1b1b);border:1px solid #999}
.datebox{position:absolute;left:0;top:22px;width:75px;height:72px;background:var(--accent);color:#fff;text-align:center}
.datebox b{display:block;font-size:32px;line-height:38px;margin-top:4px}
.datebox span{display:block;font-size:19px;font-weight:700;line-height:22px}
.datebox::after{content:"";position:absolute;right:-8px;top:18px;border:8px solid transparent;border-left-color:var(--accent);border-right:0}
.entry h3{position:absolute;left:92px;top:22px;font-family:'Roboto Condensed',Arial,sans-serif;font-size:17px;font-weight:700;color:#333;white-space:nowrap}
.entry p{position:absolute;left:92px;top:50px;width:349px;font-family:'Roboto Condensed','Roboto',Arial,sans-serif;font-size:13px;color:#888;line-height:22px}
.entry p span{display:block;white-space:nowrap;overflow:hidden;text-overflow:ellipsis}
.meta{position:absolute;right:0;top:112px;display:flex;gap:22px;font-size:11px;color:#888;font-style:italic;white-space:nowrap}
.meta span{display:flex;align-items:center;gap:6px}
.meta .dot{width:14px;height:14px;border-radius:50%;background:#999;display:inline-block}
.meta .sq{width:14px;height:12px;background:#999;display:inline-block}
.meta b{font-weight:700;color:#555}
.show-all{width:441px;height:26px;line-height:26px;background:#e3e3e3;text-align:center;font-size:12px;font-style:italic;color:#555;margin-top:12px}

/* customers */
.customers-line{left:141px;top:1636px;width:918px;height:3px;background:#333}
.customers-badge{left:470px;top:1619px;width:262px;height:38px;background:#444;color:#fff;font-family:'Roboto Condensed',Arial,sans-serif;font-size:25px;font-weight:700;text-align:center;line-height:38px;clip-path:polygon(20px 0,calc(100% - 20px) 0,100% 50%,calc(100% - 20px) 100%,20px 100%,0 50%)}
.customer{top:1730px;width:190px;text-align:center;font-family:'Roboto Condensed',Arial,sans-serif;font-size:31px;font-weight:700;color:#333;letter-spacing:1px}

/* footer */
.site-footer{left:0;top:1878px;width:1200px;height:272px;background:var(--footer);color:#fff}
.f-col{top:37px}
.f-col h4{font-family:'Roboto Condensed',Arial,sans-serif;font-size:20px;font-weight:700}
.f-col p{font-size:12.5px;color:#ddd;line-height:20px;margin-top:10px}
.f-col ul{list-style:none;margin-top:10px}
.f-col li{font-size:12.5px;color:#ddd;line-height:22.6px}
.input{margin-top:18px;width:184px;height:29px;border-radius:15px;background:#2e2e2e;color:#ddd;font-size:12px;line-height:29px;padding-left:14px;box-shadow:inset 0 1px 3px rgba(0,0,0,.6)}
.btn-sub{margin-top:16px;width:78px;height:27px;border-radius:14px;background:var(--accent);color:#fff;font-size:11px;font-weight:700;text-align:center;line-height:27px}
.contact-row{display:flex;align-items:center;gap:12px;font-size:12.5px;color:#ddd;height:28.5px;white-space:nowrap}
.contact-row i{flex:none;width:13px;height:13px;background:#fff;display:inline-block;border-radius:2px}
.contact-row em{font-style:normal;color:var(--accent);text-decoration:underline;margin-left:-8px}
.contact-row strong{font-weight:400;color:var(--accent);margin-left:-8px}

/* bottom bar */
.bottom{left:0;top:2150px;width:1200px;height:81px;background:#fff}
.bottom-ledge{left:790px;top:2150px;width:410px;height:26px;background:var(--footer);clip-path:polygon(0 0,100% 0,100% 100%,40px 100%)}
.ledge-text{left:860px;top:2156px;color:#fff;font-size:11px;font-weight:700}
.to-top{left:573px;top:2130px;width:34px;height:34px;border-radius:50%;background:#fff;border:2px solid #ccc}
.social{left:862px;top:2187px;display:flex;gap:10px}
.social i{width:28px;height:28px;border-radius:4px;display:block}
.copyright{left:0;top:2197px;width:1200px;text-align:center;font-size:11.5px;color:#777}
</style>
</head>
<body>

<header class="site-header abs">
  <div class="brand abs" style="left:141px;top:22px"><span class="brand-dot"></span><span class="brand-name">Cloudvane</span></div>
  <nav class="main-nav abs">
    <a class="active">About</a><a>Support</a><a>Deployment</a><a>Training</a><a>Development</a><a>Contact Us</a>
  </nav>
</header>

<section class="hero abs">
  <div class="hero-art abs" role="img" aria-label="Smartphone with colourful app icon blocks bursting out of its screen"></div>
  <div class="hero-title abs cond">
    <div class="l1">BRISBANE'S LEADING</div>
    <div class="l2"><span>VELMORA SUITE</span> SPECIALISTS</div>
  </div>
</section>

<section class="intro abs">
  <h1>“Lorem Ipsum is simply dummy text of the printing and typesetting industry.”</h1>
  <p>Lorem Ipsum has been the industry's standard dummy text ever since the 1500s,<br>when an unknown printer took a galley of type and scrambled it to make a type specimen book.</p>
  <span class="btn-dark cond">ASK YOUR QUESTION ?</span>
</section>
<div class="divider-shadow abs"></div>

<div class="tile tile-blue abs">
  <svg width="76" height="76" viewBox="0 0 76 76"><circle cx="38" cy="38" r="34" fill="none" stroke="#fff" stroke-width="5"/><circle cx="38" cy="38" r="25" fill="#fff"/><text x="38" y="50" text-anchor="middle" font-family="Roboto,Arial,sans-serif" font-size="34" font-weight="700" fill="#1e73bb">$</text></svg>
  <p>Lorem ipsum dolor sit amet, Lorem Ipsum, dizgi ve baskı endüstrisinde kullanılan consectetur adipiscing elit ...</p>
  <h3>Save Money</h3>
</div>
<div class="tile tile-green abs">
  <svg width="76" height="76" viewBox="0 0 76 76" fill="none" stroke="#fff" stroke-width="3"><circle cx="38" cy="38" r="34" stroke-width="4"/><circle cx="38" cy="38" r="6" fill="#fff"/><circle cx="38" cy="15" r="4"/><circle cx="58" cy="30" r="4"/><circle cx="52" cy="55" r="4"/><circle cx="24" cy="55" r="4"/><circle cx="18" cy="30" r="4"/><path d="M38 32V19M43 35l11-4M42 43l7 9M34 43l-7 9M33 35l-11-4"/></svg>
  <p>Lorem ipsum dolor sit amet, Lorem Ipsum, dizgi ve baskı endüstrisinde kullanılan consectetur adipiscing elit ...</p>
  <h3>Collaborate</h3>
</div>
<div class="tile tile-orange abs">
  <svg width="76" height="76" viewBox="0 0 76 76" fill="#fff"><rect x="6" y="58" width="5" height="10"/><rect x="15" y="52" width="5" height="16"/><rect x="24" y="46" width="5" height="22"/><rect x="33" y="38" width="5" height="30"/><rect x="42" y="30" width="5" height="38"/><rect x="51" y="22" width="5" height="46"/><path d="M8 48 L30 30 L40 36 L62 10" stroke="#fff" stroke-width="3" fill="none"/><path d="M54 8 L66 6 L64 18Z"/></svg>
  <p>Lorem ipsum dolor sit amet, Lorem Ipsum, dizgi ve baskı endüstrisinde kullanılan consectetur adipiscing elit ...</p>
  <h3>Grow</h3>
</div>

<section class="band abs"></section>
<div class="svc abs" style="left:150px"><h2>Run your business in the cloud</h2><p>Lorem Ipsum is simply dummy text of the printing and typesetting industry. Lorem Ipsum has been the industry's standard dummy text ever since the 1500s,</p><span class="btn-light">Explore Our Apps Solutions</span></div>
<div class="svc abs" style="left:460px"><h2>How can we help you?</h2><p>Lorem Ipsum is simply dummy text of the printing and typesetting industry. Lorem Ipsum has been the industry's standard dummy text ever since the 1500s,</p><span class="btn-light">Explore Our Apps Solutions</span></div>
<div class="svc abs" style="left:770px"><h2>Learn from Nimbus Guides</h2><p>Lorem Ipsum is simply dummy text of the printing and typesetting industry. Lorem Ipsum has been the industry's standard dummy text ever since the 1500s,</p><span class="btn-light">Explore Our Apps Solutions</span></div>

<section class="col abs" style="left:141px">
  <div class="col-head"><h2>Recent <span>Blog</span></h2><em>get latest updates</em><i></i></div>
  <article class="entry">
    <div class="thumb" role="img" aria-label="Blog post thumbnail"></div>
    <h3>The standard Lorem Ipsum used since the 1500s !!!</h3>
    <p><span>Contrary to popular belief, Lorem Ipsum is not simply random</span><span>It has roots in a piece of classical Latin literature from 45 BC...</span></p>
    <div class="meta"><span><i class="sq"></i>15 Nov, 2012</span><span><i class="dot"></i>12 Comments</span></div>
  </article>
  <article class="entry">
    <div class="thumb" role="img" aria-label="Blog post thumbnail"></div>
    <h3>The standard Lorem Ipsum used since the 1500s !!!</h3>
    <p><span>Contrary to popular belief, Lorem Ipsum is not simply random</span><span>It has roots in a piece of classical Latin literature from 45 BC...</span></p>
    <div class="meta"><span><i class="sq"></i>15 Nov, 2012</span><span><i class="dot"></i>12 Comments</span></div>
  </article>
  <div class="show-all">Show All Blog</div>
</section>

<section class="col abs" style="left:618px">
  <div class="col-head"><h2>Upcoming <span>Events</span></h2><em>get latest updates</em><i></i></div>
  <article class="entry">
    <div class="datebox"><b>20</b><span>DEC</span></div>
    <h3>The standard Lorem Ipsum used since the 1500s !!!</h3>
    <p><span>Contrary to popular belief, Lorem Ipsum is not simply random</span><span>It has roots in a piece of classical Latin literature from 45 BC...</span></p>
    <div class="meta"><span><i class="dot"></i>Live Event</span><span><i class="dot"></i>Cloudvane HQ</span><span><i class="dot"></i><b>Continue Reading...</b></span></div>
  </article>
  <article class="entry">
    <div class="datebox"><b>20</b><span>DEC</span></div>
    <h3>The standard Lorem Ipsum used since the 1500s !!!</h3>
    <p><span>Contrary to popular belief, Lorem Ipsum is not simply random</span><span>It has roots in a piece of classical Latin literature from 45 BC...</span></p>
    <div class="meta"><span><i class="dot"></i>Live Event</span><span><i class="dot"></i>Cloudvane HQ</span><span><i class="dot"></i><b>Continue Reading...</b></span></div>
  </article>
  <div class="show-all">Show All Events</div>
</section>

<div class="customers-line abs"></div>
<div class="customers-badge abs">OUR CUSTOMERS</div>
<svg class="abs" style="left:141px;top:1710px" width="30" height="60" viewBox="0 0 30 60"><path d="M28 2 L2 30 L28 58" fill="none" stroke="#888" stroke-width="2"/></svg>
<svg class="abs" style="left:1030px;top:1710px" width="30" height="60" viewBox="0 0 30 60"><path d="M2 2 L28 30 L2 58" fill="none" stroke="#888" stroke-width="2"/></svg>
<div class="customer abs" style="left:177px">BRENNICK</div>
<div class="customer abs" style="left:393px">BRENNICK</div>
<div class="customer abs" style="left:613px">BRENNICK</div>
<div class="customer abs" style="left:829px">BRENNICK</div>

<footer class="site-footer abs">
  <div class="f-col abs" style="left:160px"><h4>Newsletter !</h4><p>Enter your email to receive<br>news &amp; updates.</p><div class="input">Enter email</div><div class="btn-sub">SUBSCRIBE</div></div>
  <div class="f-col abs" style="left:436px"><h4>Quick Links</h4><ul><li>About</li><li>Support</li><li>Deployment</li><li>Training</li><li>Development</li><li>Contact Us</li></ul></div>
  <div class="f-col abs" style="left:682px"><h4>Services</h4><ul><li>Save Money</li><li>Collaborate</li><li>Grow</li></ul></div>
  <div class="f-col abs" style="left:858px;width:250px"><h4>Contact us</h4><p style="width:215px">Lorem ipsum dolor sit amet, odio consectetur adipiscing elit.</p>
    <div style="margin-top:14px">
      <div class="contact-row"><i style="border-radius:50%"></i>Lorem ipsum, State, Country</div>
      <div class="contact-row"><i></i>Tel.: <strong>+48 500 204 716</strong></div>
      <div class="contact-row"><i></i>E-mail: <em>office@cloudvane.example</em></div>
      <div class="contact-row"><i style="border-radius:50%"></i>Your-Chat-Name</div>
    </div>
  </div>
</footer>

<div class="bottom abs"></div>
<div class="bottom-ledge abs"></div>
<div class="ledge-text abs">Visit also our social profiles:</div>
<svg class="to-top abs" viewBox="0 0 34 34"><path d="M17 9 L11 16 H15 V25 H19 V16 H23Z" fill="#444"/></svg>
<div class="brand abs" style="left:141px;top:2170px"><span class="brand-dot" style="background:#222;width:40px;height:40px"></span><span class="brand-name" style="color:#222;font-size:32px">Cloudvane</span></div>
<div class="copyright abs">Copyright © 2012 Cloudvane. All Rights Reserved.</div>
<div class="social abs"><i style="background:#1b8a8a"></i><i style="background:#3b5998"></i><i style="background:#0e76a8"></i><i style="background:#f26f21"></i><i style="background:#35aee2"></i></div>

</body>
</html>
```